wealth management firm, professional group, new model

we have a logo that works but we need a card, white background using our colors...clean look

our tag line if can be used in

The Path From Saver to Steward

```html
<!DOCTYPE html>
<html lang="en">
<head>
<meta charset="UTF-8">
<title>Arvel Wealth Partners – Business Card</title>
<link href="https://fonts.googleapis.com/css2?family=Montserrat:wght@400;500;700&display=swap" rel="stylesheet">
<style>
  :root {
    --navy: #1b2d52;
    --ink: #1f2330;
    --paper: #ffffff;
    --stage: #2b2b2d;
  }
  * { margin: 0; padding: 0; box-sizing: border-box; }
  html, body { width: 1200px; height: 839px; overflow: hidden; }
  body {
    background: var(--stage);
    font-family: "Montserrat", sans-serif;
    position: relative;
  }

  /* Front: vertical white card */
  .card-front {
    position: absolute;
    left: 90px; top: 105px;
    width: 360px; height: 630px;
    background: var(--paper);
    border-radius: 26px;
    color: var(--navy);
    text-align: center;
    display: flex; flex-direction: column; align-items: center;
    padding-top: 120px;
  }
  .brand-name {
    font-weight: 400;
    font-size: 54px;
    letter-spacing: 22px;
    margin-right: -22px;
    line-height: 1;
  }
  .brand-sub {
    font-weight: 400;
    font-size: 15px;
    letter-spacing: 4.5px;
    margin-top: 16px;
  }
  .tagline {
    font-size: 10.5px;
    letter-spacing: 2.4px;
    margin-top: 14px;
    white-space: nowrap;
  }
  .person-name {
    font-weight: 700;
    font-size: 30px;
    margin-top: 78px;
    letter-spacing: 0.5px;
  }
  .person-role {
    font-size: 15px;
    color: var(--ink);
    margin-top: 4px;
  }
  .icon-row {
    display: flex; align-items: center; gap: 6px;
    margin-top: 16px;
  }
  .icon-row .rule { width: 34px; height: 2px; background: var(--navy); margin: 0 8px; }
  .icon { width: 26px; height: 26px; }
  .contact {
    margin-top: 14px;
    font-size: 16px;
    line-height: 1.6;
    color: var(--ink);
  }
  .divider { width: 230px; height: 2px; background: var(--navy); margin-top: 22px; }
  .address {
    margin-top: 20px;
    font-size: 16px;
    line-height: 1.55;
    color: var(--ink);
  }

  /* Back: horizontal navy card */
  .card-back {
    position: absolute;
    left: 520px; top: 250px;
    width: 620px; height: 360px;
    background: var(--navy);
    border-radius: 26px;
    color: var(--paper);
    display: flex; flex-direction: column; align-items: center; justify-content: center;
    text-align: center;
  }
  .card-back .brand-name { font-size: 76px; letter-spacing: 30px; margin-right: -30px; }
  .card-back .brand-sub { font-size: 20px; letter-spacing: 6px; margin-top: 22px; }
  .card-back .tagline { font-size: 14px; letter-spacing: 3px; margin-top: 16px; }
</style>
</head>
<body>

<section class="card-front">
  <div class="brand-name">ARVEL</div>
  <div class="brand-sub">WEALTH PARTNERS</div>
  <div class="tagline">THE PATH FROM SAVER TO STEWARD</div>

  <div class="person-name">DORIAN KELLER</div>
  <div class="person-role">Managing Director</div>

  <div class="icon-row">
    <span class="rule"></span>
    <svg class="icon" viewBox="0 0 26 26" aria-label="Phone">
      <circle cx="13" cy="13" r="13" fill="#1b2d52"/>
      <path d="M7 10c0-2 2-3 6-3s6 1 6 3l-2 1-1-2h-6l-1 2zM8 13h10v5H8z" fill="#fff"/>
    </svg>
    <svg class="icon" viewBox="0 0 26 26" aria-label="Email">
      <circle cx="13" cy="13" r="13" fill="#1b2d52"/>
      <rect x="6.5" y="8.5" width="13" height="9" fill="none" stroke="#fff" stroke-width="1.6"/>
      <path d="M6.5 8.5l6.5 5 6.5-5" fill="none" stroke="#fff" stroke-width="1.6"/>
    </svg>
    <svg class="icon" viewBox="0 0 26 26" aria-label="Website">
      <circle cx="13" cy="13" r="13" fill="#1b2d52"/>
      <circle cx="13" cy="13" r="6.5" fill="none" stroke="#fff" stroke-width="1.5"/>
      <ellipse cx="13" cy="13" rx="2.8" ry="6.5" fill="none" stroke="#fff" stroke-width="1.2"/>
      <path d="M6.5 13h13" stroke="#fff" stroke-width="1.2"/>
    </svg>
    <span class="rule"></span>
  </div>

  <div class="contact">
    123 456 789<br>
    info@arvelwealth.com<br>
    arvelwealth.com
  </div>
  <div class="divider"></div>
  <div class="address">
    Your address, City<br>
    State, Zip 1234
  </div>
</section>

<section class="card-back">
  <div class="brand-name">ARVEL</div>
  <div class="brand-sub">WEALTH PARTNERS</div>
  <div class="tagline">THE PATH FROM SAVER TO STEWARD</div>
</section>

</body>
</html>
```